Grafic Ad for a Printmagazine about Tractor Vehicles

We need for a Geman Printmagazine about Tractors a Grafic Design in different sizes. Our Website and corporate Design: https://www.kalvimo.de You can work with the uploaded files . The round Logo with shaking hands should be included in your Designs somehow. Perhaps as a transparent in the background or placed in a corner. The Font used for the URL is Days (typelodge.com/days.font) Please use this Font or a other similar for the URL "kalvimo.de" and expand it to "www.kalvimo.de/traktorwert" For the other Text parts (first line) and (second line) you can use a other font which you prefer. We need the grafics as .jpg in the pixel sizes: 472x496, 437x614, 307x437 (Print would be DPI 300). Goal is a eye-catching design for the later print ad. Have fun and be creative ;)

Logo Text

"Traktor Bewertung" (first line), " Kurzgutachen für Verkauf, Kauf oder Versicherung" (second line), "www.kalvimo.de/traktorwert" (third line)

Logo styles of interest
Pictorial/Combination Logo
Font styles to use
Other font styles liked:
• Days.tff for the URL

Colors
0054AA
0677BA
7BADD7
CADEEF
E8F1F8
0094D4
00A9DD
6FCCEA
C7EBF8
E9F6FB

```html
<!DOCTYPE html>
<html lang="de">
<head>
<meta charset="utf-8">
<title>Traktor Bewertung – Anzeigen</title>
<link href="https://fonts.googleapis.com/css2?family=Days+One&display=swap" rel="stylesheet">
<style>
  :root{
    --page:#e6e6e6;
    --white:#ffffff;
    --blue-deep:#0677ba;
    --blue-mid:#0094d4;
    --blue-sky:#6fccea;
    --blue-pale:#c7ebf8;
    --blue-mist:#e9f6fb;
    --brown:#3b2417;
    --grey-title:#4a4a4a;
  }
  html,body{margin:0;padding:0;width:1200px;height:2371px;overflow:hidden;background:var(--page);}
  body{position:relative;font-family:"Days One",sans-serif;}
  .ad{position:absolute;overflow:hidden;
      background:linear-gradient(90deg,#1e82c6 0%,#5fa9dc 35%,#9fd9f1 65%,#d9f0fa 100%);}
  .ad > *{position:absolute;margin:0;}
  .wave{left:0;top:0;width:100%;height:100%;}
  .brand{color:var(--blue-deep);white-space:nowrap;display:flex;align-items:center;gap:.35em;}
  .brand-dot{width:.7em;height:.7em;border-radius:50%;background:var(--blue-mid);display:inline-block;}
  .stars{display:block;}
  .headline{white-space:nowrap;color:var(--grey-title);line-height:1;}
  .headline .accent{color:var(--blue-deep);}
  .photo{border-radius:40% 45% 30% 30%/50% 50% 35% 35%;
         background:radial-gradient(ellipse at 55% 45%,#3f7ed0 0%,#1f5bab 55%,rgba(31,91,171,0) 75%);}
  .url-pill{border-radius:999px;display:flex;align-items:center;justify-content:center;
            background:linear-gradient(180deg,#8fcff0 0%,#2d8fd3 45%,#1c74bf 100%);
            box-shadow:0 6px 10px rgba(0,40,90,.35), inset 0 2px 0 rgba(255,255,255,.8);
            color:var(--white);white-space:nowrap;}
  .services{color:var(--brown);text-align:center;line-height:1;white-space:nowrap;}
  .icon{fill:none;stroke:var(--brown);stroke-width:2.2;stroke-linecap:round;stroke-linejoin:round;}
  .col{left:0;width:100%;}
</style>
</head>
<body>

<svg width="0" height="0" style="position:absolute" aria-hidden="true">
  <defs>
    <linearGradient id="starFill" x1="0" y1="0" x2="0" y2="1">
      <stop offset="0" stop-color="#6fccea"/>
      <stop offset="1" stop-color="#1f82c8"/>
    </linearGradient>
    <symbol id="star" viewBox="0 0 100 100">
      <path d="M50 5L61 38H96L68 59L79 93L50 72L21 93L32 59L4 38H39Z" fill="url(#starFill)" stroke="#ffffff" stroke-width="2"/>
    </symbol>
    <symbol id="starRow" viewBox="0 0 300 90">
      <use href="#star" x="0" y="28" width="60" height="60"/>
      <use href="#star" x="240" y="28" width="60" height="60"/>
      <use href="#star" x="45" y="12" width="75" height="75"/>
      <use href="#star" x="180" y="12" width="75" height="75"/>
      <use href="#star" x="105" y="0" width="90" height="90"/>
    </symbol>
    <symbol id="iconTag" viewBox="0 0 48 48">
      <path class="icon" d="M6 8H26L42 24L26 40L6 24Z" transform="rotate(-20 24 24)"/>
      <circle class="icon" cx="14" cy="14" r="2.5"/>
      <path class="icon" d="M18 26L30 20M20 31L32 25"/>
    </symbol>
    <symbol id="iconCash" viewBox="0 0 48 48">
      <rect class="icon" x="3" y="16" width="32" height="20" rx="2"/>
      <rect class="icon" x="7" y="20" width="24" height="12" rx="1"/>
      <path class="icon" d="M19 22V30M16 26H13M25 26H22"/>
      <path class="icon" d="M30 16L38 9H45M38 9V20"/>
    </symbol>
    <symbol id="iconShield" viewBox="0 0 48 48">
      <path class="icon" d="M24 4L40 10V22C40 33 33 40 24 44C15 40 8 33 8 22V10Z"/>
      <path class="icon" d="M24 9L35 13.5V22C35 30 30 35 24 38.5C18 35 13 30 13 22V13.5Z"/>
      <path class="icon" d="M18 23L22.5 27.5L30 19"/>
    </symbol>
  </defs>
</svg>

<!-- Large landscape ad -->
<section class="ad ad-large" style="left:96px;top:94px;width:990px;height:704px;">
  <svg class="wave" viewBox="0 0 990 704" preserveAspectRatio="none" aria-hidden="true">
    <path d="M0 0H990V215C870 195 700 205 520 240C330 280 170 300 0 280Z" fill="var(--white)"/>
    <path d="M0 170C70 235 190 255 310 255C190 268 70 260 0 240Z" fill="var(--blue-mid)"/>
    <path d="M620 205C780 175 900 180 990 195V230C900 212 780 205 620 205Z" fill="var(--blue-pale)"/>
  </svg>
  <div class="brand" style="left:64px;top:158px;font-size:26px;"><span class="brand-dot"></span>kalvimo.de</div>
  <svg class="stars" style="left:504px;top:20px;width:358px;height:108px;" aria-hidden="true"><use href="#starRow"/></svg>
  <h1 class="headline" style="right:60px;top:140px;font-size:46px;">Traktor <span class="accent">Bewertung</span></h1>
  <div class="photo" role="img" aria-label="Foto eines blauen Oldtimer-Traktors" style="left:138px;top:320px;width:354px;height:234px;"></div>
  <div class="url-pill" style="left:52px;top:588px;width:606px;height:60px;font-size:32px;">www.kalvimo.de/traktorwert</div>
  <div class="services" style="left:688px;top:0;width:260px;height:704px;">
    <p style="position:absolute;left:0;width:100%;top:258px;margin:0;font-size:22px;">Kurzgutachen für</p>
    <svg style="position:absolute;left:104px;top:318px;width:54px;height:54px;"><use href="#iconTag"/></svg>
    <p style="position:absolute;left:0;width:100%;top:383px;margin:0;font-size:31px;">Verkauf,</p>
    <svg style="position:absolute;left:104px;top:434px;width:54px;height:54px;"><use href="#iconCash"/></svg>
    <p style="position:absolute;left:0;width:100%;top:497px;margin:0;font-size:31px;">Kauf oder</p>
    <svg style="position:absolute;left:104px;top:548px;width:54px;height:54px;"><use href="#iconShield"/></svg>
    <p style="position:absolute;left:0;width:100%;top:611px;margin:0;font-size:31px;">Versicherung</p>
  </div>
</section>

<!-- Medium ad -->
<section class="ad ad-medium" style="left:192px;top:882px;width:799px;height:760px;">
  <svg class="wave" viewBox="0 0 799 760" preserveAspectRatio="none" aria-hidden="true">
    <path d="M0 0H799V265C700 245 560 250 420 280C260 315 130 330 0 315Z" fill="var(--white)"/>
    <path d="M0 195C60 265 160 290 275 292C160 305 60 298 0 280Z" fill="var(--blue-mid)"/>
    <path d="M500 250C630 225 730 228 799 240V275C730 258 630 252 500 250Z" fill="var(--blue-pale)"/>
  </svg>
  <div class="brand" style="left:40px;top:164px;font-size:29px;"><span class="brand-dot"></span>kalvimo.de</div>
  <svg class="stars" style="left:338px;top:34px;width:358px;height:104px;" aria-hidden="true"><use href="#starRow"/></svg>
  <h1 class="headline" style="left:280px;top:153px;font-size:46px;">Traktor <span class="accent">Bewertung</span></h1>
  <div class="photo" role="img" aria-label="Foto eines blauen Oldtimer-Traktors" style="left:82px;top:360px;width:360px;height:246px;"></div>
  <div class="url-pill" style="left:40px;top:658px;width:460px;height:46px;font-size:26px;">www.kalvimo.de/traktorwert</div>
  <div class="services" style="left:513px;top:0;width:260px;height:760px;">
    <p style="position:absolute;left:0;width:100%;top:295px;margin:0;font-size:24px;">Kurzgutachen für</p>
    <svg style="position:absolute;left:101px;top:361px;width:58px;height:58px;"><use href="#iconTag"/></svg>
    <p style="position:absolute;left:0;width:100%;top:428px;margin:0;font-size:31px;">Verkauf,</p>
    <svg style="position:absolute;left:101px;top:481px;width:58px;height:58px;"><use href="#iconCash"/></svg>
    <p style="position:absolute;left:0;width:100%;top:548px;margin:0;font-size:31px;">Kauf oder</p>
    <svg style="position:absolute;left:101px;top:599px;width:58px;height:58px;"><use href="#iconShield"/></svg>
    <p style="position:absolute;left:0;width:100%;top:668px;margin:0;font-size:31px;">Versicherung</p>
  </div>
</section>

<!-- Small ad -->
<section class="ad ad-small" style="left:239px;top:1734px;width:705px;height:494px;">
  <svg class="wave" viewBox="0 0 705 494" preserveAspectRatio="none" aria-hidden="true">
    <path d="M0 0H705V160C610 145 480 150 350 170C220 190 110 200 0 190Z" fill="var(--white)"/>
    <path d="M0 110C50 160 140 180 245 180C140 192 50 188 0 175Z" fill="var(--blue-mid)"/>
    <path d="M440 150C560 130 650 132 705 140V170C650 156 560 150 440 150Z" fill="var(--blue-pale)"/>
  </svg>
  <div class="brand" style="left:43px;top:101px;font-size:19px;"><span class="brand-dot"></span>kalvimo.de</div>
  <svg class="stars" style="left:373px;top:18px;width:231px;height:68px;" aria-hidden="true"><use href="#starRow"/></svg>
  <h1 class="headline" style="left:335px;top:98px;font-size:30px;">Traktor <span class="accent">Bewertung</span></h1>
  <div class="photo" role="img" aria-label="Foto eines blauen Oldtimer-Traktors" style="left:71px;top:222px;width:266px;height:180px;"></div>
  <div class="url-pill" style="left:31px;top:420px;width:363px;height:40px;font-size:19px;">www.kalvimo.de/traktorwert</div>
  <p class="services" style="left:414px;top:174px;font-size:23px;">Kurzgutachen für</p>
  <svg style="position:absolute;left:412px;top:240px;width:46px;height:46px;"><use href="#iconTag"/></svg>
  <p class="services" style="left:477px;top:249px;font-size:23px;">Verkauf,</p>
  <svg style="position:absolute;left:412px;top:331px;width:46px;height:46px;"><use href="#iconCash"/></svg>
  <p class="services" style="left:477px;top:341px;font-size:23px;">Kauf oder</p>
  <svg style="position:absolute;left:412px;top:423px;width:46px;height:46px;"><use href="#iconShield"/></svg>
  <p class="services" style="left:477px;top:433px;font-size:23px;">Versicherung</p>
</section>

</body>
</html>
```